Copper lark buildworks

Copper lark buildworks is a small construction company.
Who is a licenced builder, Carpenter, joiner,
working on heritage ,new build, speacial projects and sometimes furniture

Industry/Entity Type

Construction

```html
<!DOCTYPE html>
<html lang="en">
<head>
<meta charset="utf-8">
<title>Copper lark buildworks – business card</title>
<link href="https://fonts.googleapis.com/css2?family=Lato:wght@400;700&display=swap" rel="stylesheet">
<style>
  :root {
    --leaf: #8cc63f;
    --ink: #1c1c1c;
    --paper: #ffffff;
    --stage: #e9e7e2;
  }
  * { box-sizing: border-box; margin: 0; padding: 0; }
  html, body { width: 1200px; height: 880px; overflow: hidden; }
  body {
    background: var(--stage);
    font-family: "Lato", Arial, sans-serif;
    position: relative;
  }
  .card {
    position: absolute;
    width: 620px;
    height: 354px;
    border-radius: 26px;
    box-shadow: 0 10px 28px rgba(0,0,0,.18);
    overflow: hidden;
  }
  .card--front { left: 80px; top: 60px; background: var(--leaf); }
  .card--back  { left: 500px; top: 466px; background: var(--paper); }

  .brand {
    display: flex;
    align-items: center;
    gap: 10px;
    font-weight: 700;
    letter-spacing: .3px;
    white-space: nowrap;
  }
  .brand__dot {
    border-radius: 50%;
    flex: none;
  }
  .card--front .brand {
    position: absolute; left: 0; right: 0; top: 138px;
    justify-content: center;
    font-size: 34px; color: var(--ink);
  }
  .card--front .brand__dot { background: var(--paper); width: 18px; height: 18px; }
  .front__web {
    position: absolute; left: 0; right: 0; top: 212px;
    text-align: center;
    color: var(--paper);
    font-size: 13px;
    letter-spacing: 4px;
  }

  .card--back .brand {
    position: absolute; left: 34px; top: 196px;
    font-size: 21px; color: var(--leaf);
  }
  .card--back .brand__dot { background: var(--ink); width: 12px; height: 12px; }
  .back__divider {
    position: absolute; left: 330px; top: 78px;
    width: 1.5px; height: 200px; background: var(--leaf);
  }
  .contact {
    position: absolute; left: 362px; top: 92px;
    color: var(--ink);
  }
  .contact__name { font-size: 22px; font-weight: 400; line-height: 1; }
  .contact__name .surname { color: var(--leaf); }
  .contact__role { font-size: 14px; margin-top: 3px; margin-bottom: 14px; }
  .contact__list { list-style: none; }
  .contact__item {
    display: flex; align-items: center; gap: 8px;
    font-size: 14px; line-height: 1; margin-bottom: 7px;
  }
  .contact__icon { width: 18px; height: 18px; flex: none; }
</style>
</head>
<body>

<section class="card card--front" aria-label="Card front">
  <div class="brand"><span class="brand__dot"></span>Copper lark buildworks</div>
  <p class="front__web">www.copperlarkbuild.com</p>
</section>

<section class="card card--back" aria-label="Card back">
  <div class="brand"><span class="brand__dot"></span>Copper lark buildworks</div>
  <div class="back__divider"></div>
  <div class="contact">
    <p class="contact__name">Milo <span class="surname">Hartwell</span></p>
    <p class="contact__role">President</p>
    <ul class="contact__list">
      <li class="contact__item">
        <svg class="contact__icon" viewBox="0 0 18 18" aria-hidden="true">
          <circle cx="9" cy="9" r="8" fill="none" stroke="var(--leaf)" stroke-width="1.4"/>
          <rect x="6.2" y="4.5" width="5.6" height="9" rx="1" fill="none" stroke="var(--leaf)" stroke-width="1.2"/>
        </svg>
        0431627905
      </li>
      <li class="contact__item">
        <svg class="contact__icon" viewBox="0 0 18 18" aria-hidden="true">
          <circle cx="9" cy="9" r="8" fill="none" stroke="var(--leaf)" stroke-width="1.4"/>
          <rect x="4.8" y="6" width="8.4" height="6" fill="none" stroke="var(--leaf)" stroke-width="1.2"/>
          <path d="M4.8 6 L9 9.4 L13.2 6" fill="none" stroke="var(--leaf)" stroke-width="1.2"/>
        </svg>
        hello@copperlarkmail.com
      </li>
      <li class="contact__item">
        <svg class="contact__icon" viewBox="0 0 18 18" aria-hidden="true">
          <circle cx="9" cy="9" r="8" fill="none" stroke="var(--leaf)" stroke-width="1.4"/>
          <circle cx="9" cy="9" r="4.4" fill="none" stroke="var(--leaf)" stroke-width="1.1"/>
          <path d="M4.6 9 H13.4 M9 4.6 V13.4" stroke="var(--leaf)" stroke-width="1"/>
        </svg>
        www.copperlarkbuild.com
      </li>
    </ul>
  </div>
</section>

</body>
</html>
```